Residential Mortgage Leader needs Wordpress Design

Looking for a home page website design for a client. We develop using the WordPress platform and would prefer the design be at least loosely based on an existing WordPress template. Attached files have many notes from our creative brief with client. The site must be responsive. Approved, basic wireframe attached. There is room for interpretation.

Existing web site: http://www.marisolkettering.example/

The Marisol Kettering Team relies on strong systems to deliver an on-time, done-right, friendly experience. Marisol offers mortgages and refinancing services throughout the United States. She is a successful Brookvale Funding agent who strives to be an active part of her community. She would like to focus the site on her team, rather than just her.

Difference makers...
When you work with the Marisol Kettering team you get a high level of expertise and a friendly experience.

She has amazing credentials. Marisol is widely recognized as a top producer for her company, and has earned a number of awards and honors for her customer service.

Marisol's team is very engaged and enjoys sharing social comments or photos from their community.

Imagery:
* Friendly, warm imagery, preferably of her team or an image to represent her team
* Clean and crisp
* Professional / Experts in mortgage and refinance
* Clean / Good use of white space
Updates

When possible, please use imagery from the DFW area. The client mentioned they would prefer not to see stock images. Thanks.

Amend that- creative use of stock images, however, is fine. A few designs have used stock imagery, but in a well-considered manner.

We added some photos and graphics that are local. We are Dallas / Ft. Worth, Plano, Frisco, Texas. We also added some examples of photos to use for the "In the Community" area. Stock photos of business folks just doesn't fit there. Thanks!

Target Market(s)

They service a lot of builders, but also work with homeowners. Their typical client is usually a woman searching for mortgage services online. She typically has a family and may refer her husband to Marisol's team. Keep in mind, however, they also see a number of other scenarios. Most of their clients are middle to high-end borrowers.

Industry/Entity Type

It Company

Requirements
Must have
• Design should be developed using program such as Photoshop or Fireworks or Illustrator as last preference. Ideally, the design would be based on an existing responsive WordPress theme, which we would customize. You must include the name of the target theme. The footer should include lots of space for disclaimers and legal language. Site navigation should include these choices: "Home, About, Builders, Mortgage Info, Approval, Blog, Contact"
Nice to have
• Blog, social media and photos area. Use of the already approved style prototype with colors and fonts (Lato- a Google font, Times New Roman and Cookie-a decorative Google font). However, we are open to interpretation.
Should not have
• Hard to read fonts or a lack of white space.

```html
<!DOCTYPE html>
<html lang="en">
<head>
<meta charset="utf-8">
<title>Brookvale Funding – Marisol Kettering</title>
<link href="https://fonts.googleapis.com/css2?family=Cookie&family=Lato:wght@300;400;700&family=Tinos&display=swap" rel="stylesheet">
<style>
  :root{
    --black:#000;
    --header:#050505;
    --hero:#2b2b2b;
    --red:#c8321e;
    --blue:#2a8fc0;
    --ink:#333;
    --muted:#8a8a8a;
    --band:#f1f1f1;
    --panel:#ececec;
    --footer:#2c2c2c;
    --footer-text:#d8d8d8;
    --bottom:#222;
    --white:#fff;
  }
  *{box-sizing:border-box;margin:0;padding:0}
  html,body{width:996px;height:1200px;overflow:hidden}
  body{font-family:"Lato",sans-serif;color:var(--ink);background:var(--white)}
  .wrap{width:815px;margin:0 auto;position:relative}

  .topbar{height:27px;background:var(--black);border-bottom:1px solid #222;color:var(--white);font-size:13px}
  .topbar .wrap{display:flex;justify-content:flex-end;align-items:center;height:27px}

  .masthead{height:87px;background:var(--header);border-bottom:1px solid #333}
  .masthead .wrap{display:flex;justify-content:space-between;align-items:center;height:87px}
  .brand{display:flex;align-items:center;gap:10px}
  .brand-mark{width:22px;height:22px;background:var(--red)}
  .brand-name{font-weight:700;font-size:25px;color:var(--white);line-height:1}
  .brand-sub{display:block;font-size:12px;font-weight:700;color:var(--white);margin-top:4px}
  .nav{display:flex;gap:6px;list-style:none;font-size:14px;color:var(--white)}
  .nav li{padding:4px 10px}
  .nav .current{background:var(--red)}

  .hero{height:289px;background:var(--hero);position:relative;overflow:hidden}
  .hero-copy{position:absolute;left:0;top:68px;width:310px;color:var(--white);font-size:11px;line-height:15px}
  .hero-title{font-family:"Cookie",cursive;font-size:44px;font-weight:400;line-height:1;margin-bottom:16px}
  .hero-copy p+p{margin-top:15px}
  .hero-photo{position:absolute;right:0;top:22px;width:400px;height:267px;background:linear-gradient(180deg,#4a4a4a,#1d1d1d 70%);border-radius:120px 120px 0 0}

  .tagline{height:70px;background:var(--band);border-bottom:1px solid #d0d0d0}
  .tagline .wrap{display:flex;align-items:center;justify-content:space-between;height:70px;padding-left:17px}
  .tagline h2{font-family:"Cookie",cursive;font-weight:400;font-size:29px;color:#111}
  .btn{background:var(--red);color:var(--white);font-family:"Tinos",serif;font-size:15px;padding:9px 9px;border:1px solid #a82414}

  .highlights{height:184px;border-bottom:1px solid #ccc}
  .highlights .wrap{display:flex;padding-top:43px}
  .feature{font-size:10px;line-height:15px;color:var(--muted);font-weight:300}
  .feature h3{display:flex;align-items:center;gap:10px;font-family:"Tinos",serif;font-weight:400;font-size:21px;color:var(--red);margin-bottom:10px}
  .feature-1{width:310px;margin-left:8px}
  .feature-2{width:210px;margin-left:40px;margin-top:-4px}
  .feature-3{width:210px;margin-left:34px;margin-top:-4px}

  .updates{height:242px;background:var(--panel)}
  .updates .wrap{display:flex;padding-top:27px}
  .col-title{font-family:"Tinos",serif;font-weight:400;font-size:20px;color:var(--blue);margin-bottom:12px}
  .blog{width:299px}
  .post h4{font-weight:400;font-size:15px;color:#444;margin-bottom:3px}
  .post{margin-bottom:10px}
  .post-body{display:flex;gap:12px;font-size:11px;line-height:15px;color:var(--muted)}
  .thumb{width:45px;height:43px;border:1px solid #ccc;background:linear-gradient(135deg,#dfe7f1,#5b7fb1)}
  .thumb-target{background:radial-gradient(circle,#c8321e 30%,#f3f3f3 60%)}
  .social{width:284px}
  .social-item{display:flex;gap:13px;margin-bottom:8px}
  .social-icon{width:45px;height:43px;border:1px solid #ccc;background:var(--white);display:flex;align-items:center;justify-content:center}
  .social-item h4{font-weight:400;font-size:15px;color:#444;margin:1px 0 5px}
  .social-item p{font-size:11px;color:var(--muted)}
  .community .grid{display:grid;grid-template-columns:repeat(3,73px);gap:7px}
  .community .tile{height:67px;border:1px solid #ccc}

  .site-footer{height:246px;background:var(--footer);color:var(--footer-text)}
  .site-footer .wrap{display:flex;padding-top:32px}
  .agent{display:flex;width:380px;margin-left:18px}
  .agent-photo{width:120px;height:137px;background:linear-gradient(180deg,#6a4a3a,#2e1f18);border:1px solid #555}
  .agent-info{margin-left:9px;font-size:11px;line-height:19px}
  .agent-info h4{font-weight:400;font-size:15px;line-height:19px;color:var(--white);margin-bottom:5px}
  .agent-info .directions{margin-top:15px;color:var(--white)}
  .footer-col h4{font-weight:400;font-size:15px;color:var(--white);margin-bottom:14px}
  .footer-links{list-style:none;font-size:11px;line-height:19px;width:220px}
  .footer-address{font-size:11px;line-height:19px}
  .lang{display:inline-flex;gap:14px;align-items:center;margin-top:14px;background:#3a3a3a;padding:5px 9px;color:var(--white)}

  .legal{height:55px;background:var(--bottom);color:#ccc;font-size:11px}
  .legal .wrap{display:flex;justify-content:space-between;align-items:center;height:55px;padding-left:19px}
  .legal-icons{display:flex;gap:5px;padding-right:15px}
  .legal-icons span{width:27px;height:27px;display:block}
</style>
</head>
<body>
  <div class="topbar"><div class="wrap">Work With Us: &nbsp;0800-5550-142-6</div></div>

  <header class="masthead">
    <div class="wrap">
      <div class="brand">
        <span class="brand-mark"></span>
        <div><span class="brand-name">Brookvale Funding</span><span class="brand-sub">A Harrowgate Capital Company</span></div>
      </div>
      <ul class="nav">
        <li class="current">Home</li><li>About Us</li><li>Buliders</li><li>Mortgage Info</li><li>Blog</li><li>Contact Us</li>
      </ul>
    </div>
  </header>

  <section class="hero">
    <div class="wrap" style="height:289px">
      <div class="hero-copy">
        <h1 class="hero-title">Earning Your Business</h1>
        <p>Lorem ipsum dolor sit amet, consectetur adipisicing elit, sed do eiusmod tempor incididunt ut labore et dolore magna aliqua.</p>
        <p>Ut enim ad minim veniam, quis nostrud exercitation ullamco laboris nisi ut aliquip ex ea commodo consequat....</p>
      </div>
      <div class="hero-photo" role="img" aria-label="Four smiling mortgage team members in business suits, arms folded"></div>
    </div>
  </section>

  <section class="tagline">
    <div class="wrap">
      <h2>Marisol Kettering... The Only Mortgage Professional You Need To Know</h2>
      <span class="btn">Get to Know Us</span>
    </div>
  </section>

  <section class="highlights">
    <div class="wrap">
      <div class="feature feature-1">
        <h3><svg width="32" height="28" viewBox="0 0 32 28"><circle cx="12" cy="7" r="5" fill="#c8321e"/><path d="M2 27c0-8 4-12 10-12s10 4 10 12z" fill="#c8321e"/><circle cx="22" cy="6" r="4.5" fill="#c8321e"/><path d="M18 14c2-1 4-1 6-1 5 0 8 4 8 13h-8" fill="#c8321e"/></svg>Our Credentials</h3>
        <p>Lorem ipsum dolor sit amet, consectetur adipisicing elit, sed do eius-mod tempor incididunt ut labore et dolore magna aliqua. Ut enim ad minim veniam, quis nostrud exercitation ullamco laboris nisi ut aliquip ex ea commodo consequat.</p>
      </div>
      <div class="feature feature-2">
        <h3><svg width="30" height="26" viewBox="0 0 30 26"><circle cx="15" cy="6" r="5.5" fill="#c8321e"/><circle cx="6" cy="15" r="5.5" fill="#c8321e"/><circle cx="24" cy="15" r="5.5" fill="#c8321e"/><circle cx="15" cy="20" r="5" fill="#c8321e"/></svg>Awards</h3>
        <p>Lorem ipsum dolor sit amet, consectetur adipisicing elit, sed do eiusmod tempor incidi-dunt ut labore et dolore magna aliqua...</p>
      </div>
      <div class="feature feature-3">
        <h3><svg width="24" height="30" viewBox="0 0 24 30" fill="none" stroke="#c8321e" stroke-width="1.8"><ellipse cx="12" cy="15" rx="10" ry="13"/><ellipse cx="12" cy="15" rx="6.5" ry="9"/><ellipse cx="12" cy="15" rx="3" ry="5"/></svg>Recognion</h3>
        <p>Lorem ipsum dolor sit amet, consectetur adipisicing elit, sed do eiusmod tempor incidi-dunt ut labore et dolore magna aliqua...</p>
      </div>
    </div>
  </section>

  <section class="updates">
    <div class="wrap">
      <div class="blog">
        <h3 class="col-title">Blog</h3>
        <div class="post">
          <h4>• Borrowing</h4>
          <div class="post-body"><div class="thumb" role="img" aria-label="Rising bar chart illustration"></div><p>Lorem ipsum dolor sit amet<br>consectetur adipiscing elit..</p></div>
        </div>
        <div class="post">
          <h4>• Best Practices</h4>
          <div class="post-body"><div class="thumb thumb-target" role="img" aria-label="Target with darts illustration"></div><p>Lorem ipsum dolor sit amet<br>consectetur adipiscing elit...<br>Sed do euismod</p></div>
        </div>
      </div>
      <div class="social">
        <h3 class="col-title">Social Icons</h3>
        <div class="social-item"><div class="social-icon"><svg width="20" height="20"><rect width="20" height="20" fill="#2a8fc0"/></svg></div><div><h4>Neighborhood Page</h4><p>Lorem ipsum dolor sit amet...</p></div></div>
        <div class="social-item"><div class="social-icon"><svg width="20" height="20"><circle cx="10" cy="10" r="10" fill="#2a8fc0"/></svg></div><div><h4>Quick Updates</h4><p>Lorem ipsum dolor sit amet...</p></div></div>
        <div class="social-item"><div class="social-icon"><svg width="22" height="22" viewBox="0 0 22 22" fill="none" stroke="#2a8fc0" stroke-width="3"><circle cx="4" cy="18" r="2.5" fill="#2a8fc0" stroke="none"/><path d="M2 10a10 10 0 0 1 10 10"/><path d="M2 3a17 17 0 0 1 17 17"/></svg></div><div><h4>Rss</h4><p>Lorem ipsum dolor sit amet...</p></div></div>
      </div>
      <div class="community">
        <h3 class="col-title">In The Community</h3>
        <div class="grid">
          <div class="tile" role="img" aria-label="Large group of neighbors in colorful shirts" style="background:linear-gradient(135deg,#e8b34a,#3d7cc4)"></div>
          <div class="tile" role="img" aria-label="Team members standing together indoors" style="background:linear-gradient(135deg,#d9d4cc,#5a4a3e)"></div>
          <div class="tile" role="img" aria-label="Group gathered outside a local building" style="background:linear-gradient(135deg,#c9cbd0,#7a5c52)"></div>
          <div class="tile" role="img" aria-label="Circle of people looking down at the camera" style="background:linear-gradient(135deg,#f0ece6,#6b5a4c)"></div>
          <div class="tile" role="img" aria-label="Hands stacked together in teamwork" style="background:linear-gradient(135deg,#e8a88c,#c06a4a)"></div>
          <div class="tile" role="img" aria-label="Friends jumping with arms raised" style="background:linear-gradient(135deg,#f6f6f6,#d2b04a)"></div>
        </div>
      </div>
    </div>
  </section>

  <footer class="site-footer">
    <div class="wrap">
      <div class="agent">
        <div class="agent-photo" role="img" aria-label="Portrait of Marisol Kettering, branch manager"></div>
        <div class="agent-info">
          <h4>Marisol Kettering<br>Branch Manager</h4>
          Office: 469.555.0148<br>Cell: 866.555.0193<br>mkettering@brookvalefunding.example<br>NMLS: 40219<br>2840 Larkspur Commons, Ste. 210<br>Frisco, TX 75033
          <div class="directions">Directions</div>
        </div>
      </div>
      <div class="footer-col">
        <h4>LINKS</h4>
        <ul class="footer-links"><li>Home</li><li>About</li><li>Builders</li><li>Mortgage Info</li><li>Approval</li><li>Blog</li><li>Contact Us</li></ul>
      </div>
      <div class="footer-col">
        <h4>ADDRESS</h4>
        <div class="footer-address">
          Our Address<br>Corporate Office - 9400 Halvern Road,<br>Suite 600 Dallas, Texas 75251<br><br>Tel : 1-800-555-0127<br>Email : Contact Brookvale Funding
        </div>
        <div class="lang">Language... <svg width="10" height="6"><path d="M1 1l4 4 4-4" stroke="#fff" fill="none"/></svg></div>
      </div>
    </div>
  </footer>

  <div class="legal">
    <div class="wrap">
      <span>Copyright © 2013 Brookvale Funding. All Rights Reserved</span>
      <div class="legal-icons">
        <span style="background:#4aa8d8"></span><span style="background:#3b5f9a"></span><span style="background:#e8762a"></span><span style="background:#fff"></span>
      </div>
    </div>
  </div>
</body>
</html>
```